Single brochure for international companies in the financial sector

We need to update a brochure 4 pages presenting our company. We are a financial engineering company. The final design must provide financial security, service and trust. you will find the current brochure copy. Our color code is Orange (RGB 235/100/68), Black, White and Gray. photos show the visual of the site, but it is not mandatory to keep them.

Target Market(s)

wealth management professionals

Industry/Entity Type

Finance

Requirements
Must have
• Logo Corvelle Capital all text in the document color Orange Corvelle (RGB 235/100/68)
Nice to have
• Vista Font
Should not have
• images / pictures of people

```html
<!DOCTYPE html>
<html lang="fr">
<head>
<meta charset="utf-8">
<title>Corvelle Capital — Couverture</title>
<link rel="stylesheet" href="https://fonts.googleapis.com/css2?family=Jost:wght@300;400;500&display=swap">
<style>
  :root {
    --orange-corvelle: #eb6444;
    --white: #ffffff;
    --ink: #1a1a1a;
  }
  html, body {
    margin: 0;
    padding: 0;
    overflow: hidden;
  }
  .cover {
    position: relative;
    width: 785px;
    height: 1200px;
    background: var(--orange-corvelle);
    font-family: "Jost", "Futura", sans-serif;
    overflow: hidden;
  }
  .brand {
    position: absolute;
    left: 0;
    right: 0;
    top: 388px;
    text-align: center;
    color: var(--white);
    font-weight: 300;
  }
  .brand__name {
    margin: 0;
    font-size: 74px;
    line-height: 1;
    letter-spacing: 0.36em;
    margin-right: -0.36em;
    font-weight: 300;
  }
  .brand__suffix {
    margin: 34px 0 0;
    font-size: 48px;
    line-height: 1;
    letter-spacing: 0.3em;
    margin-right: -0.3em;
    font-weight: 300;
  }
  .legal {
    position: absolute;
    left: 0;
    right: 0;
    top: 842px;
    text-align: center;
    color: var(--ink);
    font-size: 14.5px;
    line-height: 31px;
    font-weight: 400;
  }
  .legal p {
    margin: 0;
  }
  .legal__web {
    margin-top: 28px !important;
    font-size: 12px;
    font-weight: 500;
  }
</style>
</head>
<body>
  <main class="cover">
    <header class="brand">
      <h1 class="brand__name">CORVELLE</h1>
      <p class="brand__suffix">CAPITAL</p>
    </header>
    <footer class="legal">
      <p>Corvelle Capital SA. Capital : 400 000 Euros</p>
      <p>RCS Paris : 812 447 503</p>
      <p>Code Banque (CIB) : 14726</p>
      <p class="legal__web">www.corvellecapital.com</p>
    </footer>
  </main>
</body>
</html>
```